Need label design for car cleaning spray bottle, big opportunity for repeat work

This is the first label design for a large assortment of car cleaning products. This design will be vital as it will set the design style for the remaining products. There is large opportunity for repeat work to the winning designer. For this first product we plan to call it "Interior Cleaner". We have the template label which we have attached to the project. The product is geared towards the market of Vornik car owners, and our logo also utilizes a similar font to what Vornik's company font uses.

We are looking to only update the design/format of the label. We will keep all text the same or modify it once the design is final. We will need to use our brand logo (attached).

We are looking for a minimalistic style design. Currently the label reads horizontally but we have noticed that the most successful brands that sell online have a vertical style design. We have attached some examples of brands such as "Gleam Crest" and "Kestrel" which sell primarily on Marketlane.example and have tens of thousands of reviews. We'd like to try and copy this label format as it seems very successful for these brands.

We are big fans of the minimal style that the brand "AutoLume" uses. Their label design emphasizes the name of the particular product in black text on a white background. The remainder of the label is color coded, and all of their products have a different color code while following the same diagonal design style. See attached examples.

So that being said, we would like to combine these 2 concepts, vertical alignment style with the minimalistic label design.

We are thinking of making the entire label white, and having an accent color like 1 large stripe that goes across the bottle, it would be an iconic part of the design as we will repeat this design across multiple products, similar to the AutoLume brand bundle example we attached. This specific product will be pink liquid (as you can tell the accent color is pink on the label).

We'd like to add a dynamic QR code (can use placeholder) on the label so customers can be directed to our website easily or any other page we choose in the future. We will also need a UPC barcode label (can use placeholder)

Target Market(s)

Vornik car owners

Industry/Entity Type

Car Detailing Products

Font styles to use
Sans Serif

Colors
E54698
E96AAD
F1A4CE
F9D9EA
FCEFF6

Requirements
Must have
• minimalistic design
Should not have
• no designs similar to brands like polish fellows, brantwells, or any older brands in the category

```html
<!DOCTYPE html>
<html lang="en">
<head>
<meta charset="utf-8">
<title>Halvex All-Purpose Cleaner Label</title>
<link rel="stylesheet" href="https://fonts.googleapis.com/css2?family=Montserrat:wght@300;500;600;700;900&display=swap">
<style>
  :root {
    --pink-strong: #E54698;
    --pink-mid: #E96AAD;
    --pink-soft: #F1A4CE;
    --pink-pale: #F9D9EA;
    --pink-mist: #FCEFF6;
    --ink: #111114;
    --label-white: #ffffff;
    --backdrop: #dcd9db;
  }
  * { margin: 0; padding: 0; box-sizing: border-box; }
  html, body {
    width: 1200px;
    height: 800px;
    overflow: hidden;
    background: var(--backdrop);
    font-family: "Montserrat", sans-serif;
  }
  .canvas {
    width: 1200px;
    height: 800px;
    display: flex;
    align-items: center;
    justify-content: center;
  }
  .label {
    width: 360px;
    height: 720px;
    display: block;
    filter: drop-shadow(0 6px 18px rgba(0,0,0,0.12));
  }
  .label-base { fill: var(--label-white); }
  .band-fill { fill: url(#pinkSweep); }
  .band-edge { fill: var(--pink-strong); opacity: 0.9; }
  .band-highlight { fill: var(--pink-soft); opacity: 0.45; }
  .brand-name {
    font-family: "Montserrat", sans-serif;
    font-weight: 600;
    font-size: 24px;
    fill: var(--ink);
  }
  .product-line {
    font-family: "Montserrat", sans-serif;
    font-weight: 300;
    font-size: 44px;
    fill: var(--ink);
  }
  .product-name {
    font-family: "Montserrat", sans-serif;
    font-weight: 900;
    font-size: 84px;
    fill: var(--ink);
  }
  .badge-disc { fill: var(--ink); stroke: var(--pink-mist); stroke-width: 2.5; }
  .badge-text {
    font-family: "Montserrat", sans-serif;
    font-weight: 700;
    fill: var(--label-white);
    text-anchor: middle;
  }
  .badge-text .small { font-size: 7px; }
  .badge-text .medium { font-size: 10px; font-weight: 900; }
  .badge-text .large { font-size: 13px; font-weight: 900; }
  .net-contents {
    font-family: "Montserrat", sans-serif;
    font-weight: 500;
    font-size: 9px;
    fill: var(--pink-mist);
    text-anchor: middle;
  }
  .site-address {
    font-family: "Montserrat", sans-serif;
    font-weight: 700;
    font-size: 12px;
    fill: var(--label-white);
    text-anchor: middle;
  }
</style>
</head>
<body>
<main class="canvas">
  <svg class="label" viewBox="0 0 360 720" xmlns="http://www.w3.org/2000/svg" aria-label="Halvex all-purpose cleaner label">
    <defs>
      <linearGradient id="pinkSweep" x1="0" y1="0" x2="1" y2="1">
        <stop offset="0" stop-color="#E96AAD"/>
        <stop offset="0.55" stop-color="#E54698"/>
        <stop offset="1" stop-color="#d93a8b"/>
      </linearGradient>
    </defs>

    <rect class="label-base" x="0" y="0" width="360" height="720"/>

    <!-- top stripe -->
    <path class="band-fill" d="M0 0 H360 V48 C260 38 130 34 0 40 Z"/>
    <path class="band-edge" d="M0 34 C130 28 260 32 360 42 V48 C260 38 130 34 0 40 Z"/>

    <!-- brand -->
    <text class="brand-name" x="46" y="78">Halvex</text>

    <!-- vertical product name -->
    <text class="product-line" transform="translate(155 545) rotate(-90)" textLength="450" lengthAdjust="spacingAndGlyphs">ALL-PURPOSE</text>
    <text class="product-name" transform="translate(234 545) rotate(-90)" textLength="450" lengthAdjust="spacingAndGlyphs">CLEANER</text>

    <!-- bottom diagonal stripe -->
    <path class="band-fill" d="M0 650 C120 600 240 550 360 505 V720 H0 Z"/>
    <path class="band-edge" d="M0 642 C120 592 240 542 360 497 V505 C240 550 120 600 0 650 Z"/>
    <path class="band-highlight" d="M0 690 C130 640 250 590 360 550 V562 C250 602 130 652 0 702 Z"/>

    <!-- feature badges -->
    <g class="badge">
      <circle class="badge-disc" cx="52" cy="632" r="32"/>
      <text class="badge-text">
        <tspan class="medium" x="52" y="626">NON</tspan>
        <tspan class="medium" x="52" y="638">ACIDIC</tspan>
        <tspan class="small" x="52" y="648">FORMULA</tspan>
      </text>
    </g>
    <g class="badge">
      <circle class="badge-disc" cx="166" cy="588" r="32"/>
      <text class="badge-text">
        <tspan class="small" x="166" y="579">INTERIOR</tspan>
        <tspan class="large" x="166" y="593">AND</tspan>
        <tspan class="small" x="166" y="604">EXTERIOR</tspan>
      </text>
    </g>
    <g class="badge">
      <circle class="badge-disc" cx="280" cy="540" r="32"/>
      <text class="badge-text">
        <tspan class="small" x="280" y="525">REMOVES</tspan>
        <tspan class="medium" x="280" y="537">GREASE</tspan>
        <tspan class="medium" x="280" y="548">GRIME</tspan>
        <tspan class="medium" x="280" y="559">&amp; DIRT</tspan>
      </text>
    </g>

    <!-- footer -->
    <text class="net-contents" x="180" y="688">NET CONTENTS: 16 FL. OZ. (473ML)</text>
    <text class="site-address" x="180" y="708">www.halvex.example</text>
  </svg>
</main>
</body>
</html>
```